Business card design needed

I run a Beautician studio (for 7 years now)
I offer
- Velmo Body Sugaring
- Ruby Glaze
- Nails
- Facials
- Manicure
- Foot Treatment
It might not be necessary to list all those treatments?
Maybe the link to the Website is sufficient?
I leave that up to you ...
(more info on www.FernAndDewByLenka.com.au)
Velmo BodySugaring is our biggest success, It replaces waxing.
I would like to incorporate the logo into the Business Card.
We had many complaints regarding our old Business Cards as the Phone Number was to small.
On the backside, we would like a "your next Appointment" section.
Looking forward to you Design, cheers ... Lenka
Industry/Entity Type
Business
Contact Information for Business Card
Fern by Dew by Lenka
14 Korrin Sqr 3942 Dunmore
www.FernAndDewByLenka.com.au
03 9481 2267

```html
<!DOCTYPE html>
<html lang="en">
<head>
<meta charset="utf-8">
<title>Fern by Dew by Lenka – Business Cards</title>
<link rel="stylesheet" href="https://fonts.googleapis.com/css2?family=Arimo:wght@400;700&family=Cinzel:wght@500&family=PT+Sans:wght@400;700&family=Open+Sans:wght@400;600&display=swap">
<style>
  :root{
    --backdrop:#3b2b22;
    --card:#ffffff;
    --green:#0b9140;
    --orange:#ec6a24;
    --yellow:#f6c21c;
    --ink:#222222;
    --grey:#555555;
    --rule:#8a8a8a;
  }
  *{box-sizing:border-box;margin:0;padding:0}
  html,body{width:1200px;height:724px;overflow:hidden;background:var(--backdrop)}
  .canvas{position:relative;width:1200px;height:724px}
  .card{position:absolute;width:525px;height:298px;background:var(--card);border-radius:22px;overflow:hidden}
  .card--front{left:47px;top:38px;font-family:"Arimo",Arial,sans-serif;color:var(--ink)}
  .card--appt-a{left:603px;top:38px}
  .card--back{left:49px;top:370px;text-align:center;font-family:"Open Sans",Arial,sans-serif;color:var(--grey)}
  .card--appt-b{left:612px;top:373px}

  /* front */
  .accent-bar{position:absolute;left:0;top:26px;width:10px;height:46px;background:linear-gradient(var(--orange),var(--yellow))}
  .studio-name{position:absolute;left:32px;top:29px;font-size:20px;font-weight:700;color:var(--green)}
  .studio-address{position:absolute;left:32px;top:56px;font-size:14px}
  .studio-phone{position:absolute;left:32px;top:94px;font-size:18px;display:flex;align-items:center;gap:6px}
  .treatments-title{position:absolute;left:32px;top:141px;font-size:16px;font-weight:700;color:var(--green);letter-spacing:1px}
  .treatments{position:absolute;left:32px;top:163px;list-style:none;font-size:14px;line-height:21px}
  .brand-mark{position:absolute;left:330px;top:150px;width:180px;display:flex;align-items:center;gap:8px;font-size:19px;font-weight:400;color:var(--ink);line-height:1.15}
  .brand-dot{flex:none;width:22px;height:22px;border-radius:50%;background:var(--orange)}
  .footer-band{position:absolute;left:0;bottom:0;width:525px;height:40px}
  .footer-url{position:absolute;left:32px;bottom:19px;font-size:14px;color:#fff}

  /* appointment */
  .appt{font-family:"PT Sans",Arial,sans-serif;color:var(--grey);font-size:15px}
  .appt-title{position:absolute;left:35px;top:52px;font-family:"Cinzel",serif;font-weight:500;font-size:18px;color:var(--green)}
  .appt-row{position:absolute;left:35px;display:flex;align-items:center;white-space:nowrap}
  .dots{display:inline-block;border-bottom:1px dotted var(--rule);height:1px;margin:0 6px}
  .line{display:inline-block;border-bottom:1px solid var(--rule);height:1px;margin:0 4px 0 18px}
  .field-box{display:inline-block;width:95px;height:21px;border:1px solid var(--rule);border-radius:2px}
  .day{font-weight:700;font-size:15px;margin-right:9px}
  .day-box{display:inline-block;width:34px;height:20px;border:1px solid var(--rule);border-radius:2px;margin-right:9px}
  .appt-note{position:absolute;left:31px;top:249px;width:455px;font-size:13px;line-height:17px;color:#333}
  .appt-brand{position:absolute;right:56px;top:28px;display:flex;align-items:center;gap:5px;font-size:12px;color:var(--ink);width:100px;line-height:1.1}
  .appt-brand .brand-dot{width:12px;height:12px}

  /* back */
  .back-brand{position:absolute;left:0;right:0;top:85px;display:flex;justify-content:center;align-items:center;gap:12px;font-size:30px;font-weight:400;color:var(--ink)}
  .back-brand .brand-dot{width:30px;height:30px}
  .back-url{position:absolute;left:0;right:0;top:199px;font-size:15px;letter-spacing:2.3px;color:var(--ink)}
  .hours-title{position:absolute;left:0;right:0;top:231px;font-size:20px;font-weight:600;letter-spacing:1.3px}
  .hours{position:absolute;left:0;right:0;top:267px;font-size:15.5px;font-weight:600}
  .hours .sep{color:#aaa;margin:0 8px;font-weight:400}
</style>
</head>
<body>
<main class="canvas">

  <section class="card card--front">
    <div class="accent-bar"></div>
    <h1 class="studio-name">Fern by Dew by Lenka</h1>
    <p class="studio-address">14 Korrin Sqr 3942 Dunmore</p>
    <p class="studio-phone">
      <svg width="16" height="16" viewBox="0 0 16 16" aria-hidden="true"><circle cx="8" cy="8" r="7" fill="none" stroke="#0b9140" stroke-width="1.5"/><path d="M5 4.5c0 3.5 2.5 6.5 6 7l1-1.6-2-1-1 .8c-1-.5-1.8-1.4-2.2-2.3l.8-1-1-2z" fill="#0b9140"/></svg>
      03 9481 2267
    </p>
    <h2 class="treatments-title">Treatments offer</h2>
    <ul class="treatments">
      <li>• Velmo Body Sugaring</li>
      <li>• Ruby Glaze • Nails</li>
      <li>• Facials • Manicure</li>
      <li>• Foot Treatment</li>
    </ul>
    <div class="brand-mark"><span class="brand-dot"></span><span>Velmo Body Sugaring</span></div>
    <svg class="footer-band" viewBox="0 0 525 40" aria-hidden="true">
      <defs><linearGradient id="tab" x1="0" x2="1"><stop offset="0" stop-color="#ec6a24"/><stop offset="1" stop-color="#f6c21c"/></linearGradient></defs>
      <rect x="0" y="0" width="525" height="40" fill="#0b9140"/>
      <path d="M0 0H342Q332 0 326 10L320 21H0Z" fill="url(#tab)"/>
    </svg>
    <p class="footer-url">www.FernAndDewByLenka.com.au</p>
  </section>

  <section class="card card--appt-a appt">
    <h2 class="appt-title">YOUR APPOINTMENT</h2>
    <div class="appt-row" style="top:90px">Name :<span class="dots" style="width:292px;margin-left:16px"></span></div>
    <div class="appt-row" style="top:127px">Date :<span class="line" style="width:94px"></span>Time :<span class="line" style="width:88px;margin-left:6px"></span>am / pm</div>
    <div class="appt-row" style="top:163px">Next Appointment&nbsp;&nbsp;<span class="field-box"></span><span class="field-box" style="margin-left:32px"></span></div>
    <div class="appt-row" style="top:202px;left:21px"><span class="day">MON</span><span class="day-box"></span><span class="day">TUE</span><span class="day-box"></span><span class="day">WED</span><span class="day-box"></span><span class="day">THU</span><span class="day-box"></span><span class="day">FRI</span><span class="day-box"></span><span class="day">SAT</span><span class="day-box"></span></div>
    <p class="appt-note">It would be appreciated if 24 hours notice could be given if you are unable to attend an appointment</p>
  </section>

  <section class="card card--back">
    <div class="back-brand"><span class="brand-dot"></span><span>Velmo Body Sugaring</span></div>
    <p class="back-url">www.FernAndDewByLenka.com.au</p>
    <h2 class="hours-title">Hours of Operation</h2>
    <p class="hours">Mon - Fri:&nbsp; 7.30am - 7.00pm<span class="sep">|</span>Saturday: 7.30am - 12.00pm</p>
  </section>

  <section class="card card--appt-b appt">
    <div class="appt-brand"><span class="brand-dot"></span><span>Velmo Body Sugaring</span></div>
    <h2 class="appt-title">YOUR APPOINTMENT</h2>
    <div class="appt-row" style="top:88px">Name :<span class="dots" style="width:292px;margin-left:16px"></span></div>
    <div class="appt-row" style="top:125px">Date :<span class="line" style="width:94px"></span>Time :<span class="line" style="width:88px;margin-left:6px"></span>am / pm</div>
    <div class="appt-row" style="top:162px">Next Appointment&nbsp;&nbsp;<span class="field-box"></span><span class="field-box" style="margin-left:32px"></span></div>
    <div class="appt-row" style="top:200px;left:21px"><span class="day">MON</span><span class="day-box"></span><span class="day">TUE</span><span class="day-box"></span><span class="day">WED</span><span class="day-box"></span><span class="day">THU</span><span class="day-box"></span><span class="day">FRI</span><span class="day-box"></span><span class="day">SAT</span><span class="day-box"></span></div>
    <p class="appt-note" style="top:248px">It would be appreciated if 24 hours notice could be given if you are unable to attend an appointment</p>
  </section>

</main>
</body>
</html>
```